Stationery Design + Business Cards

Stationary (letterhead as A4 210x297mm and Letter 8.5"x11", preferably both master page + 2nd pages)

Also need business cards, standard size 50x88mm, can be vertical or horizontal.

You can use a front/back design for the business cards, or front only.

Looking at the uploaded file (devank, you already have that), I want it to use the first logo on the list (4 colors).

Alternative, try the grayscale version (second file).

I need the following information on the business card (in no particular order, let me know what you come up with): 

Firstname Lastlame 
Title 

Mobile +1 555-204-7391 

VelaMorn, Inc. 
24851 Birchwood Ridge Passage 
Fernhollow, ZN 46099 
Tel. +1 555-368-4172 
Fax +1 555-619-0834 

Web: www.velamorn.example 
Twitter: twitter/VelaMorn or @VelaMorn 
Facebook: facebook.com/VelaMorn 

For letterhead, just the company name, address + phone number & fax number 

If you think the phone/fax or something else should not be on the business cards, or something could be missing, let me know.

```html
<!DOCTYPE html>
<html lang="en">
<head>
<meta charset="utf-8">
<title>VelaMorn Business Cards</title>
<link rel="stylesheet" href="https://fonts.googleapis.com/css2?family=Source+Sans+3:wght@400;600;700&display=swap">
<style>
  :root {
    --stage: #000000;
    --card-top: #ffffff;
    --card-body: #6d6e71;
    --ink-light: #ffffff;
    --brand-blue: #1d4f9c;
    --brand-orange: #f07a1e;
    --rule: #b9babc;
  }
  * { margin: 0; padding: 0; box-sizing: border-box; }
  html, body { width: 1200px; height: 900px; overflow: hidden; background: var(--stage); }
  body { position: relative; font-family: "Source Sans 3", "Myriad Pro", sans-serif; color: var(--ink-light); }

  .label { position: absolute; font-weight: 700; font-size: 22.5px; text-align: center; white-space: nowrap; transform: translateX(-50%); }

  .card { position: absolute; background: var(--card-body); overflow: hidden; }
  .card-horizontal { width: 626px; height: 356px; left: 48px; }
  .card-vertical { width: 356px; height: 626px; left: 793px; top: 162px; }
  .card-top { position: absolute; left: 0; top: 0; width: 100%; background: var(--card-top); }

  .brand { position: absolute; display: flex; align-items: center; gap: 10px; white-space: nowrap; }
  .brand-dot { width: 36px; height: 36px; border-radius: 50%; background: var(--brand-orange); flex: none; }
  .brand-name { color: var(--brand-blue); font-weight: 400; font-size: 47px; line-height: 1; letter-spacing: -0.3px; }

  .t { position: absolute; white-space: nowrap; line-height: 1; }
  .c { transform: translateX(-50%); text-align: center; }
  .r { transform: translateX(-100%); text-align: right; }
  .name { font-weight: 700; font-size: 22px; }
  .title { font-weight: 400; font-size: 17px; }
  .mobile { font-weight: 700; font-size: 16.5px; }
  .small { font-weight: 600; font-size: 13px; }
  .mid { font-weight: 600; font-size: 16.5px; }
  .vsmall { font-weight: 600; font-size: 14px; }
  .divider { position: absolute; width: 1px; background: var(--rule); }
</style>
</head>
<body>

  <div class="label" style="left:354px; top:43px;">Horizontal B. card Front Only</div>
  <section class="card card-horizontal" style="top:84px;">
    <div class="card-top" style="height:116px;"></div>
    <div class="brand" style="right:36px; top:54px;"><span class="brand-dot"></span><span class="brand-name">VelaMorn</span></div>
    <div class="t c name" style="left:310px; top:168px;">Firstname Lastname</div>
    <div class="t c title" style="left:310px; top:192px;">Title</div>
    <div class="t c mobile" style="left:310px; top:212px;">Mobile +1 555-204-7391</div>
    <div class="t r small" style="left:296px; top:282px;">Web: www.velamorn.example</div>
    <div class="t r small" style="left:296px; top:298px;">Twitter: twitter/VelaMorn or @VelaMorn</div>
    <div class="t r small" style="left:296px; top:315px;">Facebook: facebook.com/VelaMorn</div>
    <div class="divider" style="left:313px; top:273px; height:66px;"></div>
    <div class="t small" style="left:330px; top:274px;">VelaMorn, Inc.</div>
    <div class="t small" style="left:330px; top:290px;">24851 Birchwood Ridge Passage</div>
    <div class="t small" style="left:330px; top:307px;">Fernhollow, ZN 46099</div>
    <div class="t small" style="left:330px; top:323px;">Tel. +1 555-368-4172, Fax +1 555-619-0834</div>
  </section>

  <div class="label" style="left:354px; top:458px;">Horizontal B. card Front Only</div>
  <section class="card card-horizontal" style="top:492px;">
    <div class="card-top" style="height:116px;"></div>
    <div class="brand" style="right:36px; top:54px;"><span class="brand-dot"></span><span class="brand-name">VelaMorn</span></div>
    <div class="t c name" style="left:310px; top:155px;">Firstname Lastname</div>
    <div class="t c title" style="left:310px; top:179px;">Title</div>
    <div class="t c mobile" style="left:310px; top:199px;">Mobile +1 555-204-7391</div>
    <div class="t c small" style="left:310px; top:251px;">VelaMorn, Inc.</div>
    <div class="t c small" style="left:310px; top:268px;">24851 Birchwood Ridge Passage, Fernhollow, ZN 46099</div>
    <div class="t c small" style="left:310px; top:285px;">Tel. +1 555-368-4172, Fax +1 555-619-0834</div>
    <div class="t c small" style="left:310px; top:310px;">Web: www.velamorn.example</div>
    <div class="t c small" style="left:310px; top:327px;">Twitter: twitter/VelaMorn or @VelaMorn&nbsp;&nbsp;Facebook: facebook.com/VelaMorn</div>
  </section>

  <div class="label" style="left:982px; top:127px;">Vertical B. card Front Only</div>
  <section class="card card-vertical">
    <div class="card-top" style="height:240px;"></div>
    <div class="brand" style="right:32px; top:170px;"><span class="brand-dot"></span><span class="brand-name">VelaMorn</span></div>
    <div class="t c name" style="left:175px; top:304px;">Firstname Lastname</div>
    <div class="t c title" style="left:175px; top:328px;">Title</div>
    <div class="t c mobile" style="left:175px; top:348px;">Mobile +1 555-204-7391</div>
    <div class="t c mid" style="left:175px; top:425px;">VelaMorn, Inc.</div>
    <div class="t c mid" style="left:175px; top:446px;">24851 Birchwood Ridge Passage</div>
    <div class="t c mid" style="left:175px; top:467px;">Fernhollow, ZN 46099</div>
    <div class="t c mid" style="left:175px; top:489px;">Tel. +1 555-368-4172</div>
    <div class="t c mid" style="left:175px; top:510px;">Fax +1 555-619-0834</div>
    <div class="t c vsmall" style="left:175px; top:552px;">Web: www.velamorn.example</div>
    <div class="t c vsmall" style="left:175px; top:571px;">Twitter: twitter/VelaMorn or @VelaMorn</div>
    <div class="t c vsmall" style="left:175px; top:589px;">Facebook: facebook.com/VelaMorn</div>
  </section>

</body>
</html>
```